Velvet Lantern rebranding my business with a new business card

I have my new logo and now I need a refresher on my business cards. I really want something fun and fresh. I like black background or anything to make the color pop.
Logo
Name: Velvet Lantern
Contact Info as stated below:
Mira Pellow
555-013-4762
Logo
Name: Velvet Lantern
Mira Pellow
555-013-4762
fb.me/VelvetLanternbyMira
Instagram: @VelvetLanternbyMira

Industry/Entity Type

Business

Contact Information for Business Card

double-sided. Logo on one side. Contact info on the other.

Requirements
Must have
• Logo
• Name: Velvet Lantern
• Contact Info as stated below:
• Mira Pellow
• 555-013-4762
• fb.me/VelvetLanternbyMira
• fb.me/VelvetLanternbyMira

```html
<!DOCTYPE html>
<html lang="en">
<head>
<meta charset="utf-8">
<title>Velvet Lantern – Business Card</title>
<link href="https://fonts.googleapis.com/css2?family=Risque&family=Poppins:wght@400&display=swap" rel="stylesheet">
<style>
  :root {
    --stage: #1e1e1e;
    --teal: #2fb7a0;
    --teal-deep: #22ab98;
    --teal-light: #37c2ab;
    --white: #ffffff;
    --ring-pink: #f2a6bf;
    --ink: #3d3d3d;
    --logo-ink: #5a3d4a;
  }
  * { box-sizing: border-box; margin: 0; padding: 0; }
  html, body { width: 1200px; height: 897px; overflow: hidden; background: var(--stage); }
  .stage { position: relative; width: 1200px; height: 897px; }

  .card {
    position: absolute; left: 341px; width: 506px; height: 288px;
    border-radius: 14px; overflow: hidden;
  }
  .card--front { top: 154px; }
  .card--back { top: 464px; background: var(--white); }

  .front-pattern {
    position: absolute; inset: 0;
    background: linear-gradient(180deg, var(--teal-light) 0%, var(--teal-deep) 100%);
  }

  .logo-badge {
    position: absolute; width: 148px; height: 148px; border-radius: 50%;
    background: var(--white);
    box-shadow: inset 0 0 0 5px var(--white), inset 0 0 0 7px var(--ring-pink);
    display: flex; align-items: center; justify-content: center; text-align: center;
    font-family: "Risque", serif; font-size: 21px; line-height: 1.1; color: var(--logo-ink);
  }
  .card--front .logo-badge { left: 179px; top: 70px; }

  .title-band {
    position: absolute; left: 0; top: 86px; width: 100%; height: 77px;
    background: var(--teal);
  }
  .badge-gap {
    position: absolute; left: 175px; top: 41px; width: 156px; height: 156px;
    border-radius: 50%; background: var(--white);
  }
  .card--back .logo-badge { left: 179px; top: 45px; }

  .band-text {
    position: absolute; top: 104px; font-family: "Risque", serif;
    font-size: 25px; letter-spacing: 1px; color: var(--white); line-height: 1.5;
  }
  .holder-name { left: 20px; }
  .holder-role { left: 348px; }

  .contact {
    position: absolute; top: 210px; left: 0; width: 100%;
    font-family: "Poppins", sans-serif; font-size: 12.5px; color: var(--ink);
  }
  .contact-row { display: flex; align-items: center; height: 20px; }
  .contact-left { width: 235px; text-align: right; }
  .contact-icons { display: flex; gap: 4px; margin: 0 6px 0 7px; }
  .icon {
    width: 10px; height: 10px; border-radius: 2px; background: var(--teal);
    display: flex; align-items: center; justify-content: center;
  }
</style>
</head>
<body>
<main class="stage">

  <section class="card card--front" aria-label="Card front">
    <div class="front-pattern" role="img" aria-label="Faint pattern of ice cream cones and popsicles on teal"></div>
    <div class="logo-badge">Velvet<br>Lantern</div>
  </section>

  <section class="card card--back" aria-label="Card back">
    <div class="title-band"></div>
    <div class="badge-gap"></div>
    <div class="logo-badge">Velvet<br>Lantern</div>
    <p class="band-text holder-name">Mira Pellow</p>
    <p class="band-text holder-role">Owner</p>

    <div class="contact">
      <div class="contact-row">
        <span class="contact-left">555-013-4762</span>
        <span class="contact-icons">
          <span class="icon">
            <svg width="8" height="8" viewBox="0 0 10 10"><path d="M2.2 1 L3.8 1 L4.4 3 L3.4 3.8 Q4.3 5.7 6.2 6.6 L7 5.6 L9 6.2 L9 7.8 Q8.8 9 7.6 9 Q1 8.4 1 2.4 Q1 1.2 2.2 1 Z" fill="#fff"/></svg>
          </span>
          <span class="icon"></span>
        </span>
        <span>me/VelvetLanternbyMira</span>
      </div>
      <div class="contact-row">
        <span class="contact-left">info@mirapellow.com</span>
        <span class="contact-icons">
          <span class="icon">
            <svg width="8" height="8" viewBox="0 0 10 10"><rect x="1" y="2.2" width="8" height="5.6" rx="0.6" fill="#fff"/><path d="M1.4 2.8 L5 5.4 L8.6 2.8" stroke="#2fb7a0" stroke-width="0.9" fill="none"/></svg>
          </span>
          <span class="icon"></span>
        </span>
        <span>@VelvetLanternbyMira</span>
      </div>
    </div>
  </section>

</main>
</body>
</html>
```